Business Cards for company that supports physicians that do medical research

Need to create a business card for Qorvel Studies (www.qorvelstudies.example), a company devoted to supporting physicians who conduct medical research. The form of the card should match the message of research and information quest. I have provided the logo of the company as an uploaded file. Designs should be simple and slick aimed at very high end clients.

Target Market(s)

Medical doctors that are also researchers

Industry/Entity Type

Medical

Contact Information for Business Card

Should feature logo and fields for personal info:
Name/title
Phone /email

Font styles to use
Serif
Sans Serif

Requirements
Must have
• Qorvel logo and fields for personal info:
• Name: Bertrand Okonfu
• Title: VP Research and Senior Analyst
• Phone: 555-203-4719
• email: info@qorvelstudies.example
Nice to have
• Interesting cards that I've seen:
• 1- all black/charcoal or very dark background
• 2- Plastic - semi-transparent
• 3- non-standard height-width ratios
• 4- Functional cards -- USB drive incorporated
Should not have
• Too busy; needs to stay very simple

```html
<!DOCTYPE html>
<html lang="en">
<head>
<meta charset="utf-8">
<title>Qorvel Studies – Business Card</title>
<link href="https://fonts.googleapis.com/css2?family=Lato:wght@400;700&display=swap" rel="stylesheet">
<style>
  :root {
    --backdrop: #e9e6e1;
    --card: #2b323a;
    --card-shadow: rgba(0,0,0,0.35);
    --blue: #1e88c8;
    --green: #5cc44f;
    --white: #ffffff;
    --rule: #d9dde1;
  }
  * { margin: 0; padding: 0; box-sizing: border-box; }
  html, body {
    width: 1200px; height: 1000px; overflow: hidden;
    background: var(--backdrop);
    font-family: "Lato", Arial, sans-serif;
  }
  .canvas { position: relative; width: 1200px; height: 1000px; }
  .card {
    position: absolute; left: 265px; width: 667px; height: 397px;
    background: var(--card); border-radius: 22px; overflow: hidden;
    box-shadow: 0 10px 24px var(--card-shadow);
  }
  .card--front { top: 73px; }
  .card--back { top: 533px; }

  .brand-name {
    position: absolute; color: var(--green); font-weight: 700;
    white-space: nowrap; line-height: 1;
  }
  .card--front .brand-name { left: 38px; top: 172px; font-size: 44px; }
  .card--back .brand-name { left: 0; right: 0; top: 172px; text-align: center; font-size: 62px; }

  .person { position: absolute; left: 372px; top: 121px; right: 0; }
  .person__name { color: var(--blue); font-size: 22px; font-weight: 700; }
  .person__title { color: var(--green); font-size: 16.5px; margin-top: 6px; }
  .person__rule { height: 1px; background: var(--rule); margin-top: 9px; }

  .contact { position: absolute; left: 372px; top: 199px; list-style: none; }
  .contact__item {
    display: flex; align-items: center; gap: 9px;
    color: var(--white); font-size: 16.5px; height: 26px;
  }
  .contact__icon { width: 14px; height: 14px; fill: var(--blue); flex: none; }

  .card__photo {
    position: absolute; left: 230px; top: 0; right: 0; bottom: 0;
    background: radial-gradient(ellipse at 70% 45%, rgba(70,80,90,0.55), rgba(43,50,58,0) 65%),
                linear-gradient(160deg, rgba(60,68,78,0.35), rgba(43,50,58,0));
  }
</style>
</head>
<body>
<main class="canvas">
  <section class="card card--front">
    <div class="brand-name">Qorvel Studies</div>
    <div class="person">
      <h1 class="person__name">Bertrand Okonfu</h1>
      <p class="person__title">VP Research and Senior Analyst</p>
      <div class="person__rule"></div>
    </div>
    <ul class="contact">
      <li class="contact__item">
        <svg class="contact__icon" viewBox="0 0 16 16"><path d="M3 2h3l1.5 3.5-2 1.3a8 8 0 0 0 3.7 3.7l1.3-2L14 10v3a1 1 0 0 1-1 1A11 11 0 0 1 2 3a1 1 0 0 1 1-1z"/></svg>
        555-203-4719
      </li>
      <li class="contact__item">
        <svg class="contact__icon" viewBox="0 0 16 16"><path d="M1 3h14v10H1z M1.5 3.5 8 9l6.5-5.5" stroke="#2b323a" stroke-width="1.2"/></svg>
        info@qorvelstudies.example
      </li>
      <li class="contact__item">
        <svg class="contact__icon" viewBox="0 0 16 16"><circle cx="8" cy="8" r="6.5"/><path d="M8 1.5v13M1.5 8h13" stroke="#2b323a" stroke-width="1.1"/></svg>
        www.qorvelstudies.example
      </li>
    </ul>
  </section>

  <section class="card card--back">
    <div class="card__photo" role="img" aria-label="Faint photo of a stethoscope resting on a keyboard"></div>
    <div class="brand-name">Qorvel Studies</div>
  </section>
</main>
</body>
</html>
```